Need website for Dating "Game" App

I need a one or two page website for a new dating "game" app (patent pending) called wooSpark.net. The game will be "interactive" and is designed to be a fun, safe and nonthreatening way to help two people get to know more about each other "before making a face to face date". The App will be configured somewhat like a dating app/website where members browse profiles to find someone they are interested in getting to know.
I am looking for a design that will capture the attention of singles who are tired of wasting time on face to face dates with individuals they are not compatible with. This website will be used as somewhat of a launch page for a Fundlaunch campaign because the app is still in the development stage.

Target Market(s)

Single daters who are looking for a compatible mate

Industry/Entity Type

Dating

Number of Pages Required

2 page

Requirements
Must have
• Mention that the game is Patent Pending
• Must be whimsical but with a classy-clean look (the game is designed to be fun)
• I have a 30 second video completed that I would like incorporated on the website.
• Logo colors must stay the same
• Page must direct to my upcoming Fundlaunch campaign - (Dating App is still in development stage)
Nice to have
• 1. The game will populate relationship/lifestyle like questions to two players who opt to play the game together. The design could possibly have some fun relationship questions "raining" down on the page.
• 2. Tag line...MEET - PLAY - CONNECT
• Meet - Browse profiles to find someone whom you want to get to know better and invite them to play!
• Play - Many dating sites take you through a grueling set of questions before you upload a profile. You are then matched with individuals that an "algorithm" determines you are most compatible with. The problem with this method is that only the algorithm knows what areas you and those individuals have in common. WooSpark.net alleviates the guesswork by placing the power of the algorithm in your hands with a fun, safe and nonthreatening game that helps you get to know your person of interest before meeting face to face!
• Date -
• 3. "Wouldn't it be great to get to know someone better before making a date?"
Should not have
• Nothing raunchy.
• I don't want the basic 'dating website' look (although I do like the "Tulip Finds Lantern" site.

```html
<!DOCTYPE html>
<html lang="en">
<head>
<meta charset="utf-8">
<title>wooSpark.net — Meet · Play · Connect</title>
<link rel="stylesheet" href="https://fonts.googleapis.com/css2?family=Open+Sans:wght@300;400;600;700&display=swap">
<style>
  :root {
    --red: #e5322d;
    --red-deep: #c8231f;
    --ink: #1a1a1a;
    --text: #444444;
    --muted: #777777;
    --white: #ffffff;
    --band: #161616;
    --field: #262626;
  }
  * { box-sizing: border-box; margin: 0; padding: 0; }
  html, body { width: 1200px; height: 2786px; overflow: hidden; }
  body {
    position: relative;
    background: var(--white);
    font-family: "Open Sans", Arial, sans-serif;
    color: var(--text);
  }
  .btn {
    position: absolute;
    display: flex; align-items: center; justify-content: center;
    font-size: 14px; font-weight: 600; letter-spacing: .5px;
    text-transform: uppercase; color: var(--white); text-decoration: none;
  }
  .btn--red { background: var(--red); }
  .btn--dark { background: var(--ink); }

  /* header */
  .site-header { position: absolute; left: 0; top: 0; width: 1200px; height: 104px; background: var(--white); }
  .brand { position: absolute; display: flex; align-items: center; gap: 8px; }
  .brand__dot { width: 22px; height: 22px; border-radius: 50%; background: var(--red); }
  .brand__name { font-size: 24px; font-weight: 700; color: var(--red); line-height: 1; }
  .brand__tag { position: absolute; font-size: 9px; font-weight: 600; color: var(--ink); white-space: nowrap; }
  .site-header .brand { left: 167px; top: 30px; }
  .site-header .brand__tag { left: 197px; top: 62px; }
  .nav { position: absolute; top: 38px; left: 607px; display: flex; gap: 40px; font-size: 15px; font-weight: 600; color: var(--ink); }
  .nav__login { left: 940px; top: 31px; width: 88px; height: 38px; font-size: 15px; }

  /* hero */
  .hero { position: absolute; left: 0; top: 104px; width: 1200px; height: 568px; }
  .hero__photo {
    position: absolute; inset: 0;
    background: radial-gradient(ellipse at 52% 45%, #a98b73 0%, #6b4d3b 35%, #2e2320 70%, #151312 100%);
  }
  .hero__kicker { position: absolute; top: 232px; width: 100%; text-align: center; font-size: 24px; color: var(--white); }
  .hero__title { position: absolute; top: 270px; width: 100%; text-align: center; font-size: 44px; font-weight: 600; color: var(--white); letter-spacing: 1px; }
  .hero__signup { left: 510px; top: 350px; width: 196px; height: 46px; }
  .hero__dots { position: absolute; top: 522px; left: 568px; display: flex; gap: 9px; }
  .hero__dots span { width: 9px; height: 9px; border-radius: 50%; background: var(--white); }
  .hero__dots span:first-child { background: var(--red); }

  /* features */
  .feature { position: absolute; width: 230px; height: 230px; border-radius: 50%; background: var(--red); top: 737px; }
  .feature::after {
    content: ""; position: absolute; left: 25px; bottom: -30px; width: 180px; height: 14px; border-radius: 50%;
    background: radial-gradient(ellipse, rgba(0,0,0,.18), rgba(0,0,0,0) 70%);
  }
  .feature svg { position: absolute; left: 75px; top: 48px; }
  .feature__label { position: absolute; top: 168px; width: 100%; text-align: center; font-size: 14px; font-weight: 600; color: var(--white); text-transform: uppercase; }
  .feature--fun { left: 191px; }
  .feature--safe { left: 485px; }
  .feature--calm { left: 779px; }

  /* step sections */
  .step { position: absolute; left: 0; width: 1200px; text-align: center; }
  .step__title { position: absolute; width: 100%; font-size: 48px; font-weight: 600; }
  .step__text { position: absolute; width: 100%; font-size: 17px; }
  .step--meet { top: 1022px; height: 433px; }
  .step--meet .step__photo { position: absolute; inset: 0; background: radial-gradient(ellipse at 60% 60%, #5a4a3d 0%, #3d332c 50%, #231d19 100%); }
  .step--meet .step__title { top: 132px; color: var(--white); }
  .step--meet .step__text { top: 221px; color: var(--white); font-weight: 300; font-size: 19px; }
  .step--meet .btn { left: 502px; top: 277px; width: 196px; height: 45px; }

  .step--play { top: 1455px; height: 457px; background: var(--white); }
  .step--play .step__title { top: 108px; color: var(--red); }
  .step--play .step__text { top: 196px; left: 200px; width: 800px; line-height: 26px; font-size: 15px; color: var(--text); }
  .step--play .btn { left: 502px; top: 285px; width: 196px; height: 45px; }

  .step--date { top: 1912px; height: 429px; }
  .step--date .step__photo { position: absolute; inset: 0; background: linear-gradient(135deg, #d8382e 0%, #c92d26 50%, #b72520 100%); }
  .step--date .step__title { top: 104px; color: var(--white); }
  .step--date .step__text { top: 198px; color: var(--white); font-size: 14px; }
  .step--date .btn { left: 502px; top: 259px; width: 196px; height: 45px; }

  /* newsletter */
  .newsletter { position: absolute; left: 0; top: 2341px; width: 1200px; height: 149px; background: var(--band); }
  .newsletter__icon { position: absolute; left: 161px; top: 63px; }
  .newsletter__label { position: absolute; left: 204px; top: 60px; font-size: 20px; color: var(--white); }
  .newsletter__field { position: absolute; left: 435px; top: 41px; width: 410px; height: 48px; background: var(--field); border: 1px solid #333; color: #666; font-size: 11px; padding: 16px 18px; }
  .newsletter .btn { left: 857px; top: 41px; width: 167px; height: 48px; }

  /* footer */
  .site-footer { position: absolute; left: 0; top: 2490px; width: 1200px; height: 296px; background: var(--white); }
  .site-footer .brand { left: 520px; top: 68px; }
  .site-footer .brand__tag { left: 550px; top: 100px; }
  .site-footer__apps { position: absolute; top: 140px; width: 100%; text-align: center; font-size: 12px; color: var(--ink); }
  .store-badge { position: absolute; top: 165px; width: 116px; height: 40px; border-radius: 6px; background: #000; border: 1px solid #888; }
  .store-badge--ios { left: 480px; }
  .store-badge--android { left: 605px; }
  .site-footer__copy { position: absolute; top: 237px; width: 100%; text-align: center; font-size: 11px; color: var(--ink); }
</style>
</head>
<body>

<header class="site-header">
  <div class="brand"><span class="brand__dot"></span><span class="brand__name">wooSpark.net</span></div>
  <span class="brand__tag">sparks before the first date</span>
  <nav class="nav"><span>Game</span><span>Dating</span><span>Members</span><span>Faq's</span></nav>
  <a class="btn btn--red nav__login">LOGIN</a>
</header>

<section class="hero">
  <div class="hero__photo" role="img" aria-label="Close-up of two people's hands cupped around a cappuccino"></div>
  <p class="hero__kicker">The game is Patent Pending</p>
  <h1 class="hero__title">MEET - PLAY - CONNECT</h1>
  <a class="btn btn--red hero__signup">Sign Up</a>
  <div class="hero__dots"><span></span><span></span><span></span><span></span></div>
</section>

<div class="feature feature--fun">
  <svg width="80" height="90" viewBox="0 0 80 90" fill="#fff">
    <polygon points="20,8 24,18 35,18 26,24 30,35 20,28 10,35 14,24 5,18 16,18"/>
    <polygon points="56,2 59,10 68,10 61,15 64,24 56,18 48,24 51,15 44,10 53,10"/>
    <polygon points="66,38 69,45 76,45 70,49 72,56 66,52 60,56 62,49 56,45 63,45"/>
    <polygon points="14,46 17,53 24,53 18,57 20,64 14,60 8,64 10,57 4,53 11,53"/>
    <path d="M40 86 L24 38 M40 86 L54 28 M40 86 L62 58 M40 86 L18 60" stroke="#fff" stroke-width="3" fill="none"/>
  </svg>
  <div class="feature__label">Fun</div>
</div>
<div class="feature feature--safe">
  <svg width="80" height="90" viewBox="0 0 80 90">
    <path d="M40 6 L72 16 L70 48 C68 68 54 80 40 86 C26 80 12 68 10 48 L8 16 Z" fill="none" stroke="#fff" stroke-width="5"/>
    <path d="M40 18 L60 24 L58 48 C56 62 48 70 40 74 Z" fill="#fff"/>
  </svg>
  <div class="feature__label">Safe</div>
</div>
<div class="feature feature--calm">
  <svg width="80" height="90" viewBox="0 0 80 90">
    <circle cx="40" cy="45" r="34" fill="none" stroke="#fff" stroke-width="7"/>
    <line x1="16" y1="21" x2="64" y2="69" stroke="#fff" stroke-width="7"/>
  </svg>
  <div class="feature__label">Nonthreatening</div>
</div>

<section class="step step--meet">
  <div class="step__photo" role="img" aria-label="Seeded bagels on a wooden table, darkened"></div>
  <h2 class="step__title">MEET</h2>
  <p class="step__text">Browse profiles to find someone whom you want to get to know better and invite them to play!</p>
  <a class="btn btn--red">Play Now</a>
</section>

<section class="step step--play">
  <h2 class="step__title">PLAY</h2>
  <p class="step__text">WooSpark.net alleviates the guesswork by placing the power of the algorithm in your hands with a fun, safe and nonthreatening game that helps you get to know your person of interest before meeting face to face!</p>
  <a class="btn btn--dark">Play Now</a>
</section>

<section class="step step--date">
  <div class="step__photo" role="img" aria-label="Couple holding hands across a café table with two coffee cups, tinted red"></div>
  <h2 class="step__title">DATE</h2>
  <p class="step__text">Wouldn't it be great to get to know someone better before making a date?"</p>
  <a class="btn btn--dark">Read More</a>
</section>

<section class="newsletter">
  <svg class="newsletter__icon" width="28" height="22" viewBox="0 0 28 22">
    <rect x="0" y="0" width="28" height="22" rx="2" fill="var(--red)"/>
    <path d="M1 2 L14 12 L27 2" fill="none" stroke="var(--band)" stroke-width="2.5"/>
  </svg>
  <span class="newsletter__label">Sign Up For Newsletter</span>
  <div class="newsletter__field">Enter Your E-mail Address</div>
  <a class="btn btn--red">Subscribe Now</a>
</section>

<footer class="site-footer">
  <div class="brand"><span class="brand__dot"></span><span class="brand__name">wooSpark.net</span></div>
  <span class="brand__tag">sparks before the first date</span>
  <p class="site-footer__apps">Our apps are avialable In :</p>
  <div class="store-badge store-badge--ios"></div>
  <div class="store-badge store-badge--android"></div>
  <p class="site-footer__copy">© 2016 Company Name &nbsp;|&nbsp; All Rights Reserved</p>
</footer>

</body>
</html>
```